Quorva - corporate Business Card

We need a good look and innovative business card for a new start up company based in Los Angeles called "Quorva". We are in a payment business, including payment card, app, and ewallet. We are expert in online payment and Card not present (CNP) transaction.
We need an innovative, modern business card.

Our logo font is Aero Matics

Target Market(s)

Startup - Bank - Online Payment - Card Manufacturing

Industry/Entity Type

Startup

Contact Information for Business Card

phone: 555 014 7396 - Address: 4172 Marlowe blvd, Larkmont, OR 97399

Requirements
Must have
• Message: innovative, professional, expert, high tech, trust, online payment expert, security
Nice to have
• no comment
Should not have
• no Comment

```html
<!DOCTYPE html>
<html lang="en">
<head>
<meta charset="utf-8">
<title>Quorva – Business Card</title>
<link href="https://fonts.googleapis.com/css2?family=Open+Sans:wght@400;600;700&display=swap" rel="stylesheet">
<style>
  :root {
    --brand-red: #b8202f;
    --card-white: #ffffff;
    --stage: #1c1c1c;
    --text-grey: #6b6b6b;
  }
  * { margin: 0; padding: 0; box-sizing: border-box; }
  html, body {
    width: 1200px; height: 741px; overflow: hidden;
    background: var(--stage);
    font-family: "Open Sans", Arial, sans-serif;
  }
  .canvas { position: relative; width: 1200px; height: 741px; }
  .card {
    position: absolute; top: 229px;
    width: 495px; height: 282px;
    border-radius: 12px; overflow: hidden;
  }
  .card--front { left: 100px; background: var(--brand-red); }
  .card--back { left: 606px; background: var(--card-white); }

  .wordmark {
    position: absolute; display: flex; align-items: center;
    font-weight: 600; letter-spacing: 1px; line-height: 1;
  }
  .wordmark__dot { border-radius: 50%; flex: none; }

  .card--front .wordmark { left: 108px; top: 99px; color: var(--card-white); }
  .card--front .wordmark__dot { width: 84px; height: 84px; background: var(--card-white); margin-right: 12px; }
  .card--front .wordmark__name { font-size: 53px; margin-top: -8px; }

  .card--back .feature-circle { position: absolute; left: 0; top: 0; }

  .card--back .wordmark { right: 28px; top: 24px; color: var(--brand-red); }
  .card--back .wordmark__dot { width: 60px; height: 60px; background: var(--brand-red); margin-right: 8px; }
  .card--back .wordmark__name { font-size: 36px; margin-top: -6px; }

  .contact {
    position: absolute; right: 28px; top: 132px;
    text-align: right; color: var(--text-grey); font-size: 13.5px; line-height: 1.2;
  }
  .contact__name { color: var(--brand-red); font-weight: 700; font-size: 17.5px; line-height: 1.1; }
  .contact__role { margin-bottom: 20px; }
  .contact__phone { margin-bottom: 22px; }
  .contact__label { color: var(--brand-red); font-weight: 700; }
</style>
</head>
<body>
<main class="canvas">
  <section class="card card--front" aria-label="Card front">
    <div class="wordmark">
      <span class="wordmark__dot"></span>
      <span class="wordmark__name">quorva</span>
    </div>
  </section>

  <section class="card card--back" aria-label="Card back">
    <svg class="feature-circle" width="495" height="282" viewBox="0 0 495 282" aria-hidden="true">
      <circle cx="92" cy="141" r="140" fill="var(--brand-red)"/>
    </svg>
    <div class="wordmark">
      <span class="wordmark__dot"></span>
      <span class="wordmark__name">quorva</span>
    </div>
    <div class="contact">
      <p class="contact__name">Dana Morrow</p>
      <p class="contact__role">Managing Director</p>
      <p class="contact__phone"><span class="contact__label">P:</span> 555 014 7396</p>
      <p class="contact__address">4172 Marlowe blvd<br>Larkmont, OR 97399</p>
    </div>
  </section>
</main>
</body>
</html>
```